Wine Label for a Sweet Wine Called "Glimmo"

We need a wine label that will be used for both a sweet red and a sweet white wine. The very important thing to remember is the target market for these wines is: young American women who love sweet wines and they also spend a lot of their money on their hair, clothes, jewelry, nails. They LOVE Glimmo (Glimmo is a word used to describe flashy accessories, jewelry, decoration.) This label needs to be eye catching, showy, fun, glittery. Please put the brand name, "Glimmo," big, and then in smaller but still readable words underneath the label or somewhere on the label: Sweet, Sophisticated, Red (or white). (An example of what I mean is attached). To differentiate between the two color wines you can suggest color changes to differentiate between the red label and the white label but the label design itself should be the same. Ultimately, the label can be the exact same label for both white and red as long as it looks good on a white wine (a greenish/yellow wine in a clear glass bottle) and a red wine (a dark color wine in a dark bottle).

I've attached an example of the text size relationship between the word Glimmo and the words to go underneath or elsewhere on the label, but you can certainly play with this-- it is just a suggestion of the text size relationship, and definitely NOT at all mandatory that you use any of these fonts.

You can pick the size of the label but try to stay within normal wine label sizes, meaning don't go bigger than approx. 3.5 inches wide and 5 inches tall.

Target Market(s)

Young American women who love sweet wines and spend a lot of money on their hair, clothes, jewelry, nails. They love Glimmo (Glimmo is a word that means flashy accessories, jewelry, decoration)

Requirements
Must have
• It needs to be flashy, glittery, fun, eye catching, memorable
Nice to have
• It shouldn't be too too ultra feminine! The target market is strong independent women and we also have men who will buy it too.

```html
<!DOCTYPE html>
<html lang="en">
<head>
<meta charset="utf-8">
<title>Glimmo Wine Label</title>
<link href="https://fonts.googleapis.com/css2?family=Cinzel:wght@500;700&display=swap" rel="stylesheet">
<style>
  :root {
    --backdrop: #050505;
    --label-black: #151414;
    --label-edge: #0c0c0c;
    --gold: #cdb56e;
    --gold-soft: #9c8548;
    --flourish: rgba(150, 150, 150, 0.22);
  }
  html, body {
    margin: 0;
    padding: 0;
    width: 1200px;
    height: 1000px;
    overflow: hidden;
    background: var(--backdrop);
  }
  .canvas {
    position: relative;
    width: 1200px;
    height: 1000px;
    background: var(--backdrop);
  }
  .wine-label {
    position: absolute;
    left: 300px;
    top: 140px;
    width: 600px;
    height: 720px;
    background: radial-gradient(ellipse at 40% 35%, #1d1c1b 0%, var(--label-black) 55%, var(--label-edge) 100%);
  }
  .label-frame {
    position: absolute;
    inset: 0;
    width: 600px;
    height: 720px;
  }
  .label-frame path {
    fill: none;
    stroke: var(--gold);
  }
  .script-flourish {
    position: absolute;
    left: 320px;
    top: 170px;
    width: 200px;
    height: 280px;
    border-radius: 50%;
    background: radial-gradient(ellipse at center, var(--flourish) 0%, rgba(150,150,150,0.06) 55%, transparent 75%);
  }
  .label-text {
    position: absolute;
    left: 60px;
    right: 60px;
    margin: 0;
    text-align: center;
    font-family: "Cinzel", Georgia, serif;
    white-space: nowrap;
  }
  .brand-name {
    top: 210px;
    font-weight: 700;
    font-size: 90px;
    letter-spacing: 3px;
    line-height: 1;
    color: var(--gold);
  }
  .wine-descriptor {
    top: 318px;
    font-weight: 700;
    font-size: 18px;
    letter-spacing: 2px;
    line-height: 1.2;
    color: var(--gold);
  }
  .vintage {
    top: 560px;
    font-weight: 500;
    font-size: 24px;
    letter-spacing: 3px;
    line-height: 1.2;
    color: var(--gold-soft);
  }
</style>
</head>
<body>
  <main class="canvas">
    <section class="wine-label">
      <svg class="label-frame" viewBox="0 0 600 720" aria-hidden="true">
        <path stroke-width="3" d="M50,18 H550 A32 32 0 0 0 582,50 V670 A32 32 0 0 0 550,702 H50 A32 32 0 0 0 18,670 V50 A32 32 0 0 0 50,18 Z"/>
        <path stroke-width="1.5" d="M54,30 H546 A24 24 0 0 0 570,54 V666 A24 24 0 0 0 546,690 H54 A24 24 0 0 0 30,666 V54 A24 24 0 0 0 54,30 Z"/>
      </svg>
      <div class="script-flourish" role="img" aria-label="Faint grey calligraphic monogram flourish behind the wine name"></div>
      <h1 class="label-text brand-name">GLIMMO</h1>
      <p class="label-text wine-descriptor">SWEET | SOPHISTICATED | RED</p>
      <p class="label-text vintage">MMXVI</p>
    </section>
  </main>
</body>
</html>
```